Wandering Rooms Stationary Set

Wandering Rooms is a bespoke interior design firm set to provide services to VIP clients with elegance and minimalism is the main theme for our stationary set. We require a full stationary set covering A4 letterhead, A4 & A3 envelopes, business cards, USB's, CDs, email signature and any other item the designer sees fit. logo is already designed and finalized, and we require the designer to use it as is without modifying the logo.

Address to be used on letterhead / business cards ...etc shall be as follows:

Phone : +971 2 518 2047
P.O. Box : 309186
Address: Block C&D, Bldg. 47, Court 12, Abu Dhabi, United Arab Emirates
Website: www.wanderingrooms-example.com

Target Market(s)

VIP Clients

Industry/Entity Type

Interior Design

Font styles to use
Other font styles liked:
• something to be unique

Colors

Designer to choose colors to be used in the design.

Requirements
Must have
• Elegant, minimalistic
Nice to have
• Simple yet elegant design having a sharp yet clean cut format
Should not have
• No additional colours, just colours that are used in the logo (silver, black or gold)

```html
<!DOCTYPE html>
<html lang="en">
<head>
<meta charset="utf-8">
<title>Wandering Rooms – Business Cards</title>
<link rel="stylesheet" href="https://fonts.googleapis.com/css2?family=Cormorant+Garamond:wght@400;500&family=Great+Vibes&display=swap">
<style>
  :root {
    --backdrop: #262626;
    --card-dark: #3a3a3a;
    --silver: #d6d6d6;
    --gold: #b39656;
    --white: #ffffff;
    --ink: #555555;
    --serif: "Cormorant Garamond", Georgia, serif;
    --script: "Great Vibes", cursive;
  }
  * { box-sizing: border-box; margin: 0; padding: 0; }
  html, body { width: 1200px; height: 960px; overflow: hidden; background: var(--backdrop); }
  .canvas { position: relative; width: 1200px; height: 960px; }

  .card {
    position: absolute;
    width: 560px;
    height: 320px;
    overflow: hidden;
  }

  /* Front */
  .card-front { left: 70px; top: 150px; background: var(--card-dark); }
  .card-front .brand {
    position: absolute; inset: 0;
    display: flex; align-items: center; justify-content: center;
    font-family: var(--serif); font-weight: 500; font-size: 44px;
    letter-spacing: 2px; color: var(--silver);
  }

  /* Back */
  .card-back { left: 570px; top: 500px; background: var(--white); }
  .card-back .swoosh { position: absolute; inset: 0; }
  .holder {
    position: absolute; right: 40px; top: 22px; text-align: right; color: var(--white);
  }
  .holder-name { font-family: var(--script); font-size: 30px; line-height: 1; }
  .holder-role { font-family: var(--serif); font-size: 14px; margin-top: 2px; }

  .card-back .brand {
    position: absolute; left: 60px; top: 168px;
    font-family: var(--serif); font-weight: 500; font-size: 34px;
    letter-spacing: 1.5px; color: var(--gold);
  }

  .address {
    position: absolute; right: 30px; top: 150px; text-align: right;
    font-family: var(--serif); font-size: 13.5px; line-height: 1.35; color: var(--ink);
  }

  .contacts {
    position: absolute; left: 40px; bottom: 28px; list-style: none;
    font-family: var(--serif); font-size: 13.5px; line-height: 1.5; color: var(--ink);
  }
  .contacts li { display: flex; align-items: center; gap: 8px; }
  .contacts svg { width: 11px; height: 11px; fill: var(--gold); flex: none; }
</style>
</head>
<body>
<main class="canvas">

  <section class="card card-front" aria-label="Business card front">
    <div class="brand">Wandering Rooms</div>
  </section>

  <section class="card card-back" aria-label="Business card back">
    <svg class="swoosh" viewBox="0 0 560 320" width="560" height="320" aria-hidden="true">
      <path d="M0 0 H560 V112 C430 72 230 74 0 150 Z" fill="var(--gold)"/>
      <path d="M40 138 C200 86 380 66 520 78 C380 74 210 96 40 138 Z" fill="var(--white)"/>
    </svg>

    <div class="holder">
      <div class="holder-name">Daniel Harper</div>
      <div class="holder-role">President</div>
    </div>

    <div class="brand">Wandering Rooms</div>

    <address class="address" style="font-style:normal">
      P.O. Box : 309186<br>
      Block C&amp;D, Bldg. 47, Court 12<br>
      Abu Dhabi, United Arab Emirate
    </address>

    <ul class="contacts">
      <li>
        <svg viewBox="0 0 24 24" aria-hidden="true"><path d="M6.6 10.8a15 15 0 0 0 6.6 6.6l2.2-2.2a1 1 0 0 1 1-.25 11.4 11.4 0 0 0 3.6.57 1 1 0 0 1 1 1V20a1 1 0 0 1-1 1A17 17 0 0 1 3 4a1 1 0 0 1 1-1h3.5a1 1 0 0 1 1 1c0 1.25.2 2.45.57 3.6a1 1 0 0 1-.25 1z"/></svg>
        +971 2 518 2047
      </li>
      <li>
        <svg viewBox="0 0 24 24" aria-hidden="true"><path d="M2 5h20v14H2z M2 5l10 8 10-8" stroke="var(--white)" stroke-width="1.5"/></svg>
        info@wanderingrooms-example.com
      </li>
      <li>
        <svg viewBox="0 0 24 24" aria-hidden="true"><circle cx="12" cy="12" r="10"/><path d="M2 12h20M12 2c3 3 3 17 0 20M12 2c-3 3-3 17 0 20" stroke="var(--white)" stroke-width="1.2" fill="none"/></svg>
        www.wanderingrooms-example.com
      </li>
    </ul>
  </section>

</main>
</body>
</html>
```